Business Card Design Project

Business Card
We are rebranding with a new logo
Industry/Entity Type
Business
Contact Information for Business Card
Dennis Morvale +61 487215963 dennis@quorv.com.au P.O. Box 872 Fernlow QLD 4309
Requirements
Must have
- Logo

```html
<!DOCTYPE html>
<html lang="en">
<head>
<meta charset="utf-8">
<title>Quorv International – Business Card</title>
<link rel="stylesheet" href="https://fonts.googleapis.com/css2?family=Roboto:wght@400;500&family=Roboto+Condensed:wght@700&display=swap">
<style>
  :root {
    --backdrop: #262626;
    --card-white: #f1f1f1;
    --blue-deep: #005a80;
    --blue-bright: #0aa7e0;
    --orange: #f7901e;
    --orange-light: #f8ad5c;
    --brand-blue: #1578a8;
    --text-light: #ffffff;
  }
  html, body {
    margin: 0;
    width: 1200px;
    height: 960px;
    overflow: hidden;
    background: var(--backdrop);
  }
  .card {
    position: absolute;
    left: 314px;
    top: 294px;
    width: 600px;
    height: 342px;
    border-radius: 22px;
    overflow: hidden;
    background: radial-gradient(circle at 55% 50%, var(--blue-bright) 0%, #0586b8 40%, var(--blue-deep) 100%);
  }
  .card__shapes {
    position: absolute;
    inset: 0;
  }
  .brand {
    position: absolute;
    left: 20px;
    width: 270px;
    top: 148px;
    display: flex;
    align-items: center;
    justify-content: center;
    gap: 10px;
  }
  .brand__dot {
    width: 16px;
    height: 16px;
    border-radius: 50%;
    background: var(--orange);
    flex: none;
  }
  .brand__name {
    font-family: "Roboto", sans-serif;
    font-weight: 500;
    font-size: 24px;
    letter-spacing: 0.5px;
    color: var(--brand-blue);
    white-space: nowrap;
  }
  .contact {
    position: absolute;
    right: 28px;
    top: 186px;
    text-align: right;
    color: var(--text-light);
    font-family: "Roboto", sans-serif;
    font-size: 14.5px;
    line-height: 19px;
  }
  .contact__name {
    font-family: "Roboto Condensed", sans-serif;
    font-weight: 700;
    font-size: 20px;
    line-height: 24px;
    margin: 0 0 4px;
  }
  .contact__address { margin: 0 0 6px; }
  .contact__line {
    display: flex;
    align-items: center;
    justify-content: flex-end;
    gap: 8px;
  }
  .contact__icon {
    width: 14px;
    height: 14px;
    flex: none;
  }
</style>
</head>
<body>
  <div class="card">
    <svg class="card__shapes" viewBox="0 0 600 342" width="600" height="342" aria-hidden="true">
      <path d="M118 0 C330 18 400 50 386 84 C360 150 292 240 252 342 L0 342 L0 0 Z" fill="var(--orange)"/>
      <path d="M118 0 C318 20 384 52 372 84 C348 150 286 240 249 342 L0 342 L0 0 Z" fill="var(--orange-light)"/>
      <path d="M118 0 C304 24 366 56 356 88 C334 152 280 240 246 342 L0 342 L0 0 Z" fill="var(--card-white)"/>
    </svg>

    <div class="brand">
      <span class="brand__dot"></span>
      <span class="brand__name">Quorv International</span>
    </div>

    <div class="contact">
      <p class="contact__name">DENNIS MORVALE</p>
      <p class="contact__address">P.O. Box 872<br>Fernlow QLD 4309</p>
      <div class="contact__line">+61 487215963
        <svg class="contact__icon" viewBox="0 0 24 24"><path fill="#fff" d="M6.6 10.8a15.1 15.1 0 0 0 6.6 6.6l2.2-2.2c.3-.3.7-.4 1-.2 1.1.4 2.3.6 3.6.6.6 0 1 .4 1 1V20c0 .6-.4 1-1 1A17 17 0 0 1 3 4c0-.6.4-1 1-1h3.5c.6 0 1 .4 1 1 0 1.3.2 2.5.6 3.6.1.3 0 .7-.2 1z"/></svg>
      </div>
      <div class="contact__line">dennis@quorv.com.au
        <svg class="contact__icon" viewBox="0 0 24 24"><path fill="#fff" d="M2 5h20v14H2z"/><path d="M2 5l10 8 10-8" fill="none" stroke="#0a7fb0" stroke-width="2"/></svg>
      </div>
      <div class="contact__line">www.quorv.com.au
        <svg class="contact__icon" viewBox="0 0 24 24"><circle cx="12" cy="12" r="10" fill="#fff"/><path d="M8 6c2 1 3 3 1 5s1 4 3 3M15 14c1 1 2 3 1 5" fill="none" stroke="#0a7fb0" stroke-width="2"/></svg>
      </div>
    </div>
  </div>
</body>
</html>
```